Quorbelline.io - Please redesign to make it look better from current design

We already have the current website, that you can access but we think it can improve from current version.
Quorbelline is a cryptocurrency hedge fund that allow you to participate in the hedge fund with cryptocurrency such as eth.
At current phase, we are doing an ICO, then we want to make sure that the website it looks professional, beautiful and trustable enough for investors after looking at our website.
Target Market(s)
Investors
Industry/Entity Type
Investment
Coding
Coded - Design and coding required
Number of Pages Required
1 page
Look and feel
Each slider illustrates characteristics of the customer's brand and the style your logo design should communicate.

```html
<!DOCTYPE html>
<html lang="en">
<head>
<meta charset="utf-8">
<title>Quorbelline — Digital Asset Management</title>
<link rel="stylesheet" href="https://fonts.googleapis.com/css2?family=Open+Sans:wght@400;600;700&display=swap">
<style>
:root{
  --navy:#1a237e;
  --blue:#0b8bcc;
  --link:#1b87c8;
  --btn:#2e9ad6;
  --text:#666;
  --dark:#222;
  --white:#fff;
  --cta:#0d0f12;
}
*{box-sizing:border-box;margin:0;padding:0}
html,body{width:1200px;height:2359px;overflow:hidden}
body{position:relative;font-family:'Open Sans',Arial,sans-serif;color:var(--text);background:var(--white)}
.abs{position:absolute}
.center{text-align:center}

/* header */
.brand{left:132px;top:60px;display:flex;align-items:center;gap:14px}
.brand-dot{width:46px;height:46px;border-radius:50%;background:var(--navy)}
.brand-name{font-size:30px;font-weight:600;color:var(--navy);letter-spacing:.5px}
.address{right:157px;top:56px;width:360px;text-align:right;font-size:10px;line-height:16px;color:#555}
.pin{left:1049px;top:56px}
.nav{right:134px;top:140px;display:flex;gap:26px;font-size:14px;color:var(--dark)}
.nav .active{color:var(--link)}

/* hero */
.hero{left:0;top:181px;width:1200px;height:432px;background:linear-gradient(100deg,#3b3a48 0%,#8a6a5a 25%,#3d5a7a 55%,#1d2d46 100%)}
.hero-shade{left:0;top:181px;width:1200px;height:432px;background:linear-gradient(180deg,rgba(0,0,0,0) 50%,rgba(0,0,0,.45) 100%)}
.hero-arrow{top:390px}
.hero-title{left:0;top:528px;width:1200px;font-size:25px;font-weight:600;color:var(--white)}
.hero-sub{left:0;top:571px;width:1200px;font-size:12.5px;color:var(--white)}

/* welcome */
.section-title{left:0;width:1200px;font-size:34px;font-weight:600;color:var(--navy)}
.welcome-title{top:682px}
.welcome-text{left:132px;top:732px;width:936px;font-size:12.5px;line-height:20.5px;color:#777;text-align:center}
.read-more{left:552px;top:838px;width:95px;height:40px;border:1px solid #ccc;font-size:12px;color:#555;line-height:38px;text-align:center}

/* process */
.process{left:0;top:958px;width:1200px;height:598px;background:var(--blue)}
.process-title{top:1028px;color:var(--white)}
.sub-heading{left:132px;font-size:20px;color:var(--white)}
.model-heading{top:1094px}
.model-text{left:132px;top:1126px;width:450px;font-size:13px;line-height:21px;color:var(--white)}
.profit-heading{top:1265px}
.profit-list{left:132px;top:1298px;list-style:none;font-size:18px;line-height:32px;color:var(--white)}
.profit-note{left:132px;top:1464px;font-size:13px;color:var(--white)}
.process-visual{left:629px;top:1100px;width:439px;height:377px;border:6px solid var(--white);background:linear-gradient(135deg,#2b3038 0%,#141a20 55%,#3c4a3e 100%)}

/* team */
.team-title{top:1625px}
.member{top:1693px;width:300px;text-align:center}
.member-photo{width:120px;height:120px;border-radius:50%;margin:0 auto;background:linear-gradient(160deg,#8a6a55,#3a2a22)}
.member-name{margin-top:12px;font-size:20px;color:var(--link)}
.member-role{font-size:14px;color:var(--dark);margin-top:1px}
.member-bio{margin:4px auto 0;width:288px;font-size:11.5px;line-height:19.6px;color:#777;text-align:justify;text-align-last:center}

/* call to action */
.cta{left:0;top:2067px;width:1200px;height:200px;background:radial-gradient(ellipse at 50% 40%,#20262c 0%,var(--cta) 70%)}
.cta-title{left:0;top:2118px;width:1200px;font-size:24px;font-weight:700;color:var(--white)}
.cta-button{left:456px;top:2158px;width:286px;height:47px;background:var(--btn);color:var(--white);font-size:20px;font-weight:700;line-height:47px;text-align:center}

/* footer */
.footer-links{left:132px;top:2289px;font-size:11.5px;color:#555;word-spacing:3px}
.copyright{left:132px;top:2315px;font-size:11.5px;color:#555}
.social{top:2298px;width:27px;height:27px;border-radius:50%}
.social-a{left:1008px;background:#3b5998}
.social-b{left:1041px;background:#1da1f2}
</style>
</head>
<body>

<header>
  <div class="abs brand"><span class="brand-dot"></span><span class="brand-name">Quorbelline</span></div>
  <p class="abs address">Suites 08-12, 9/F., East Wing, Meridian Trade Centre, Lantern Court,<br>42 Harbourview Road, Kowloon, Hong Kong.</p>
  <svg class="abs pin" width="20" height="28" viewBox="0 0 20 28"><path d="M10 1C5 1 1 5 1 10c0 7 9 17 9 17s9-10 9-17c0-5-4-9-9-9z" fill="#888"/><circle cx="10" cy="10" r="3.5" fill="#fff"/></svg>
  <nav class="abs nav"><span class="active">Home</span><span>About Us</span><span>Services</span><span>Process</span><span>Team</span><span>Contact Us</span></nav>
</header>

<section>
  <div class="abs hero" role="img" aria-label="City skyline at dusk with a glowing globe and circuit lines"></div>
  <div class="abs hero-shade"></div>
  <svg class="abs hero-arrow" style="left:6px" width="14" height="16" viewBox="0 0 14 16"><path d="M10 2L3 8l7 6" stroke="#fff" stroke-width="2.5" fill="none"/></svg>
  <svg class="abs hero-arrow" style="left:1180px" width="14" height="16" viewBox="0 0 14 16"><path d="M4 2l7 6-7 6" stroke="#fff" stroke-width="2.5" fill="none"/></svg>
  <h1 class="abs hero-title center">Digital Asset Management</h1>
  <p class="abs hero-sub center">Quorbelline enable companies and investors to facilities business operation in modern digital world, including asset management on hedge fund strategy model.</p>
</section>

<section>
  <h2 class="abs section-title welcome-title center">Welcome</h2>
  <p class="abs welcome-text">Quorbelline process and manages on hedge fund strategy models which invests in a diversified portfolio of blockchain tokens. Blockchain tokens are emerging which add a monetary incentive layer to p2p protocols and facilitate equity crowdfunding that anyone in the world can participate in. This means open source software developers can monetize their networks at the protocol level and users of the network are the equity owners of the network. For this conditions, returns will go to holders of the tokens.</p>
  <div class="abs read-more">Read more</div>
</section>

<section>
  <div class="abs process"></div>
  <h2 class="abs section-title process-title center">Process</h2>
  <h3 class="abs sub-heading model-heading">Hedge Fund Model</h3>
  <p class="abs model-text">Quorbelline run on closed-end fund （CEF）model which offers its shares to investors and utilize the fund to speculate and invest in the innovative blockchain tokens. Quorbelline will charge an upfront annual operation fee 4% of the money raised during the ICO. After that, the fund will charge a quarterly performance of 50% on the net profit made.</p>
  <h3 class="abs sub-heading profit-heading">Net Profit Distribution</h3>
  <ul class="abs profit-list">
    <li>50 % of net profit is distributed to investors</li>
    <li>0 – 5 % net profit &gt; 0% performance fee</li>
    <li>5 – 10% net profit &gt; 5% performance fee</li>
    <li>10-15 % net profit &gt; 13% performance fee</li>
    <li>&gt; 15% net profit &gt; 15% performance fee</li>
  </ul>
  <p class="abs profit-note">The remainder (50% minus performance fee, so at least 35%)  is reinvested</p>
  <div class="abs process-visual" role="img" aria-label="Tablet showing a trading order book and price chart"></div>
</section>

<section>
  <h2 class="abs section-title team-title center">Executive Team</h2>
  <div class="abs member" style="left:124px">
    <div class="member-photo" role="img" aria-label="Portrait of the director"></div>
    <h4 class="member-name">Daro Kittivanich</h4>
    <p class="member-role">Director</p>
    <p class="member-bio">As a hedge fund manager, Kittivanich is the Chief Executive Officer of Halverton Capital LLC, an investment manager of Corvane Equity Fund SP (Long-Short Equity Fund, investing in U.S. Stock Market) and Mirasol Trend Fund (Managed Futures Fund, focusing in Japanese Futures Market) Both based in Tokyo.</p>
  </div>
  <div class="abs member" style="left:449px">
    <div class="member-photo" role="img" aria-label="Portrait of the technical advisor" style="background:linear-gradient(160deg,#c9c7a8,#6d6a4f)"></div>
    <h4 class="member-name">Somchai Ruenrit</h4>
    <p class="member-role">Technical advisor</p>
    <p class="member-bio">Ruenrit has various experienced on cryptocurrency and blockchain technology. He created what was the world's 4th most valuable cryptocurrency in February 2014. He is also the world's first person to implement stealth addresses in Vexa-Wallets, improving cryptocurrency anonymity.</p>
  </div>
  <div class="abs member" style="left:775px">
    <div class="member-photo" role="img" aria-label="Portrait of the marketing consultant" style="background:linear-gradient(160deg,#9a4a3a,#3a1f1a)"></div>
    <h4 class="member-name">Wiran Phathanakul</h4>
    <p class="member-role">Marketing Consultant</p>
    <p class="member-bio">Phathanakul embeds a decade of experience in brand building, strategic planning, and marketing communication across the global agencies, such as Brightwell Group, Norland, Castell &amp; Reeve, Kiyomura. His seasoned specialty focuses on exploring a new market insight to formulate disruptive strategies</p>
  </div>
</section>

<section>
  <div class="abs cta" role="img" aria-label="Dark background with blurred trading screens and a hand"></div>
  <h2 class="abs cta-title center">FOR MORE INFORMATION</h2>
  <div class="abs cta-button">DOWNLOAD WHITEPAPER</div>
</section>

<footer>
  <p class="abs footer-links">Home &nbsp;| &nbsp;About Us &nbsp;| &nbsp;Services &nbsp;| &nbsp;Process &nbsp;| &nbsp;Team &nbsp;| &nbsp;Contact Us</p>
  <p class="abs copyright">Copyright &nbsp;©&nbsp; 2017 &nbsp;Quorbelline. &nbsp;All rights reserved.</p>
  <span class="abs social social-a"></span>
  <span class="abs social social-b"></span>
</footer>

</body>
</html>
```